Request for Business Card Design

Hi. My name is Marlene, I am looking for a new business card design for my company, Quarrow Signal Instruments, LLC. I really like the design you did for Tarsel Venture and was hoping you could do something similar using our full logo and our mark. I am also open to any raised texture design using our mark. I have attached our full logo, which would need to be somewhere on the card, as well as the mark in both outline and full form, as well as our brand colors / guide. The card does not have to be white, as long as our logo and mark appear. I actually like darker colored business cards more, but am open to all options. If you are interested in working with me, please let me know. We would also take the business card design into letterhead design if you can do that.

```html
<!DOCTYPE html>
<html lang="en">
<head>
<meta charset="utf-8">
<title>Quarrow Signal Instruments — Business Card</title>
<link href="https://fonts.googleapis.com/css2?family=Barlow:wght@400;600;700&family=Open+Sans:wght@400&display=swap" rel="stylesheet">
<style>
  :root {
    --backdrop: #3a3a3a;
    --card: #151515;
    --edge: #1c9bd4;
    --accent: #1f9fd8;
    --ink: #f2f2f2;
    --muted: #d6d6d6;
    --emboss: #2b2b2b;
    --emboss-gloss: #3d3d3d;
  }
  * { box-sizing: border-box; margin: 0; padding: 0; }
  html, body {
    width: 1200px; height: 801px; overflow: hidden;
    background: var(--backdrop);
  }
  .stage {
    position: relative; width: 1200px; height: 801px;
    display: flex; align-items: center; justify-content: center; gap: 50px;
  }
  .card {
    position: relative; width: 525px; height: 300px;
    background: var(--card);
    box-shadow: 0 3px 0 var(--edge), 0 14px 30px rgba(0,0,0,.35);
  }
  /* front */
  .brand {
    position: absolute; left: 120px; top: 58px;
    display: flex; align-items: center; gap: 18px;
  }
  .brand__dot {
    width: 58px; height: 58px; border-radius: 50%;
    background: var(--accent); flex: none;
  }
  .brand__name {
    font-family: "Barlow", sans-serif; font-weight: 700;
    font-size: 26px; line-height: 1.05; letter-spacing: 2px;
    color: var(--ink); text-transform: uppercase;
  }
  .person {
    position: absolute; left: 120px; top: 188px; text-align: right; width: 170px;
  }
  .person__name {
    font-family: "Barlow", sans-serif; font-weight: 700; font-size: 21px;
    letter-spacing: 1px; color: var(--accent); text-transform: uppercase;
  }
  .person__role {
    font-family: "Open Sans", sans-serif; font-size: 13px; color: var(--muted);
    margin-top: 2px;
  }
  .divider {
    position: absolute; left: 310px; top: 182px; width: 1px; height: 70px;
    background: var(--accent);
  }
  .contact {
    position: absolute; left: 328px; top: 184px; list-style: none;
    font-family: "Open Sans", sans-serif; font-size: 13px; color: var(--muted);
  }
  .contact li { display: flex; align-items: center; gap: 9px; height: 22px; }
  .contact svg { width: 11px; height: 11px; fill: var(--accent); flex: none; }
  /* back */
  .card--back .brand { left: 100px; top: 118px; }
  .card--back .brand__dot { background: var(--emboss); box-shadow: inset 0 1px 0 var(--emboss-gloss); }
  .card--back .brand__name { color: var(--emboss); font-size: 30px; text-shadow: 0 1px 0 var(--emboss-gloss); }
</style>
</head>
<body>
<main class="stage">
  <section class="card card--front">
    <div class="brand">
      <span class="brand__dot"></span>
      <p class="brand__name">Quarrow<br>Signal Instruments</p>
    </div>
    <div class="person">
      <p class="person__name">Dorian Vell</p>
      <p class="person__role">President</p>
    </div>
    <span class="divider"></span>
    <ul class="contact">
      <li><svg viewBox="0 0 24 24"><path d="M6.6 10.8a15.1 15.1 0 0 0 6.6 6.6l2.2-2.2a1 1 0 0 1 1-.25 11.4 11.4 0 0 0 3.6.57 1 1 0 0 1 1 1V20a1 1 0 0 1-1 1A17 17 0 0 1 3 4a1 1 0 0 1 1-1h3.5a1 1 0 0 1 1 1c0 1.25.2 2.45.57 3.57a1 1 0 0 1-.25 1z"/></svg>555-014-2287</li>
      <li><svg viewBox="0 0 24 24"><path d="M2 5h20v14H2zm2 2v.5l8 5 8-5V7l-8 5z"/></svg>d.vell@quarrow.com</li>
      <li><svg viewBox="0 0 24 24"><path d="M12 2a10 10 0 1 0 0 20 10 10 0 0 0 0-20zm6.9 6h-2.9a15.6 15.6 0 0 0-1.4-3.6A8 8 0 0 1 18.9 8zM12 4c.8 1.2 1.5 2.5 1.9 4h-3.8c.4-1.5 1.1-2.8 1.9-4zM4.3 14a8 8 0 0 1 0-4h3.4a16 16 0 0 0 0 4zm.8 2h2.9a15.6 15.6 0 0 0 1.4 3.6A8 8 0 0 1 5.1 16zM8 8H5.1a8 8 0 0 1 4.3-3.6A15.6 15.6 0 0 0 8 8zm4 12c-.8-1.2-1.5-2.5-1.9-4h3.8c-.4 1.5-1.1 2.8-1.9 4zm2.3-6H9.7a14.7 14.7 0 0 1 0-4h4.6a14.7 14.7 0 0 1 0 4zm.3 5.6A15.6 15.6 0 0 0 16 16h2.9a8 8 0 0 1-4.3 3.6zM16.3 14a16 16 0 0 0 0-4h3.4a8 8 0 0 1 0 4z"/></svg>www.quarrow.com</li>
    </ul>
  </section>
  <section class="card card--back">
    <div class="brand">
      <span class="brand__dot"></span>
      <p class="brand__name">Quarrow<br>Signal Instruments</p>
    </div>
  </section>
</main>
</body>
</html>
```